New Business Card Design for Manufacturing

We are an engineering/manufacturing company that offers Advanced machining/assembly/engineering services, as well as innovative products for the heavy duty engine cooling markets.

We are looking to get a new business card designed that is clean and modern looking, but still fits the wide range of technical/skilled work we do.

- We hope to use this design as the base for other design work in new Presentations, web, and print work.

Industry/Entity Type

Engineering

Contact Information for Business Card

Our preferred color of blue is (RGB) 22/71/159 but can vary slightly from that color. Our content will be our Logo and full company name (Vantrell Forge Works, Inc.), company address, name, job title, phone number with extension, cell number, fax number, website, and email address on the cards.
We'd like the full company name next to the logo, but we are open to other interpretations of that layout.
Preferably, we would like the back side to be clean with just our logo, and the front to contain all of the contact information.

Colors
2f74b4
0355a3
85abd2

Requirements
Must have
• - Logo, company name, needed content - We are open to interpretation beyond that.
• - Standard size business card.
• - Horizontal orientation.
• - Enough space for lengthy names / job titles (for example, a job title could read "Directory of Human Resources" or "V.P. of Governmental Affairs"). We need this to look clean, whether the title be short (CEO) or long (as described above).

```html
<!DOCTYPE html>
<html lang="en">
<head>
<meta charset="utf-8">
<title>Vantrell Forge Works – Business Card</title>
<link href="https://fonts.googleapis.com/css2?family=Roboto:wght@400;500;700&family=Roboto+Condensed:wght@500&display=swap" rel="stylesheet">
<style>
  :root {
    --brand-blue: #0e4c96;
    --paper: #f1f1f1;
    --ink-light: #ffffff;
    --backdrop: #262626;
  }
  * { margin: 0; padding: 0; box-sizing: border-box; }
  html, body { width: 1200px; height: 960px; overflow: hidden; }
  body {
    background: var(--backdrop);
    font-family: "Roboto", Arial, sans-serif;
    position: relative;
  }
  .card {
    position: absolute;
    width: 600px;
    height: 343px;
    box-shadow: 0 3px 6px rgba(0,0,0,0.5);
  }
  .card-front { left: 314px; top: 113px; background: var(--paper); }
  .card-back { left: 311px; top: 472px; background: var(--brand-blue); }

  .front-contact {
    position: absolute;
    left: 0; top: 0;
    width: 301px; height: 100%;
    background: var(--brand-blue);
    color: var(--ink-light);
    padding: 56px 0 0 48px;
  }
  .person-name {
    font-family: "Roboto Condensed", "Roboto", sans-serif;
    font-weight: 500;
    font-size: 22px;
    letter-spacing: 0.3px;
    line-height: 1;
  }
  .person-title { font-size: 14px; margin-top: 4px; }
  .address { font-size: 14px; line-height: 18px; margin-top: 68px; }
  .contact-list { list-style: none; margin-top: 11px; font-size: 14px; }
  .contact-list li { display: flex; align-items: center; height: 19px; }
  .contact-list svg { width: 13px; height: 13px; margin-right: 9px; fill: var(--ink-light); }

  .front-brand {
    position: absolute;
    left: 301px; top: 0; right: 0; bottom: 0;
    display: flex; align-items: center; justify-content: center;
  }
  .brand-lockup { display: flex; align-items: center; gap: 12px; }
  .brand-mark { width: 26px; height: 26px; background: var(--brand-blue); }
  .brand-name {
    font-weight: 700;
    font-size: 19px;
    line-height: 21px;
    color: var(--brand-blue);
    text-transform: uppercase;
  }

  .back-brand {
    position: absolute; inset: 0;
    display: flex; align-items: center; justify-content: center;
  }
  .back-brand .brand-name { color: var(--ink-light); font-size: 34px; line-height: 38px; text-align: left; }
  .back-brand .brand-mark { width: 44px; height: 44px; background: var(--ink-light); }
  .back-brand .brand-lockup { gap: 18px; }
</style>
</head>
<body>
  <section class="card card-front">
    <div class="front-contact">
      <p class="person-name">MARCUS HALE</p>
      <p class="person-title">V.P. of Governmental Affairs</p>
      <p class="address">2146 Larkspur Road<br>Fairbanks, Alaska 99712</p>
      <ul class="contact-list">
        <li><svg viewBox="0 0 16 16"><path d="M3.6 1.2l2.3 2.6-1.3 1.9c.9 2 2.4 3.5 4.4 4.4l1.9-1.3 2.6 2.3-1.4 2.4C7 13.4 2.6 9 1.2 3.1z"/></svg>907 512 4180</li>
        <li><svg viewBox="0 0 16 16"><path d="M4 0h8v16H4zM5.5 1.5v11h5v-11zM7.2 13.6h1.6v1.2H7.2z" fill-rule="evenodd"/></svg>907 388 2671</li>
        <li><svg viewBox="0 0 16 16"><path d="M1 3.5h14v9H1zM1.5 4l6.5 5 6.5-5"/><path d="M1.5 4.3L8 9.3l6.5-5" fill="none" stroke="#0e4c96" stroke-width="1.2"/></svg>marcus@vantrellforge.com</li>
        <li><svg viewBox="0 0 16 16"><circle cx="8" cy="8" r="7"/><path d="M1 8h14M8 1c-3 3.5-3 10.5 0 14M8 1c3 3.5 3 10.5 0 14" fill="none" stroke="#0e4c96" stroke-width="1"/></svg>www.vantrellforge.com</li>
      </ul>
    </div>
    <div class="front-brand">
      <div class="brand-lockup">
        <span class="brand-mark"></span>
        <p class="brand-name">Vantrell Forge<br>Works, Inc.</p>
      </div>
    </div>
  </section>

  <section class="card card-back">
    <div class="back-brand">
      <div class="brand-lockup">
        <span class="brand-mark"></span>
        <p class="brand-name">Vantrell Forge<br>Works, Inc.</p>
      </div>
    </div>
  </section>
</body>
</html>
```